Summit Builders Web Site / Business Cards

Construction Company that specializes in Water and Fire Damage, Residential ReModels, Landscaping and Building ADU (Accessory Dwelling Unit)

Growing and changing families often need additional space, and a remodeling project can often provide that. Adding a new area, or repurposing an existing one can satisfy this requirement.

Other times, homeowners want to update the look in their kitchen or bathroom with more than just a change of cabinetry or vanity doors and drawers. Whatever your needs are, Summit Builders has skilled workers who are bonded and insured, and ready to make your dreams and visions a reality.

Target Market(s)

Home Owners

Industry/Entity Type

Construction Company

Contact Information for Business Card

Center Logo with our information on the corners

Back side to be Logo Only
Contact Info
CSLB License # 2418596
info@summitbuildersca.example
www.summitbuildersca.example

Coding

Coded - Design and coding required

Number of Pages Required

5+ page

Font styles to use
Serif
Sans Serif

Requirements
Must have
• Using our Logo Colors
Home
About Us
Services
Projects / Portfolio
Contact Us
Nice to have
• Colors matching our Logo
Should not have
• Black because it doesnt match our logo

```html
<!DOCTYPE html>
<html lang="en">
<head>
<meta charset="utf-8">
<title>Summit Builders</title>
<link href="https://fonts.googleapis.com/css2?family=Montserrat:wght@400;500;600;700;800&family=Lato:wght@300;400;700&display=swap" rel="stylesheet">
<style>
:root{
  --orange:#f26522;
  --yellow:#f5d100;
  --ink:#2b2b2b;
  --text:#555;
  --muted:#888;
  --light:#f3f3f3;
  --line:#d9d9d9;
  --dark:#2a2a2a;
  --white:#fff;
}
*{margin:0;padding:0;box-sizing:border-box}
html,body{width:1200px;height:3940px;overflow:hidden}
body{position:relative;background:var(--white);font-family:"Lato",sans-serif;color:var(--text)}
.abs{position:absolute}
.head{font-family:"Montserrat",sans-serif;color:var(--ink)}
.section-title{position:absolute;left:0;width:1200px;text-align:center;font-family:"Montserrat",sans-serif;font-weight:700;font-size:36px;color:var(--ink);letter-spacing:.5px}

/* header */
.site-header{position:absolute;left:0;top:0;width:1200px;height:80px;background:var(--white)}
.brand{position:absolute;left:93px;top:18px;display:flex;align-items:center;gap:8px}
.brand-mark{width:14px;height:14px;background:var(--orange)}
.brand-name{font-family:"Montserrat",sans-serif;font-weight:700;font-size:19px;color:var(--ink);letter-spacing:.5px}
.contact-top{position:absolute;left:804px;top:9px;display:flex;gap:8px;align-items:center}
.contact-top .pin{width:22px;height:22px;background:var(--orange);display:flex;align-items:center;justify-content:center}
.contact-top .phone{font-size:13px;color:var(--ink);font-weight:700;line-height:1}
.contact-top .mail{font-size:9px;color:var(--muted)}
.quote-btn{position:absolute;left:996px;top:6px;width:110px;height:33px;background:var(--orange);color:#fff;font-size:10px;font-weight:700;display:flex;align-items:center;justify-content:center;letter-spacing:.3px}
.main-nav{position:absolute;top:62px;left:655px;display:flex;gap:0;font-size:11px;color:var(--ink)}
.main-nav a{color:var(--ink);text-decoration:none;margin-right:32px}
.main-nav a.active{color:var(--orange)}

/* hero */
.hero{position:absolute;left:0;top:80px;width:1200px;height:522px}
.hero-copy{position:absolute;left:0;width:1200px;text-align:center;color:#fff}
.hero-kicker{top:163px;font-family:"Montserrat",sans-serif;font-weight:300;font-size:30px}
.hero-title{top:192px;font-family:"Montserrat",sans-serif;font-weight:800;font-size:64px;letter-spacing:1px}
.hero-tag{top:262px;font-family:"Montserrat",sans-serif;font-weight:500;font-size:30px;color:var(--yellow)}
.btn{position:absolute;display:flex;align-items:center;justify-content:center;font-size:11px;font-weight:700;letter-spacing:.3px}
.btn-orange{background:var(--orange);color:#fff}
.btn-white{background:#fff;color:var(--ink)}
.slider-arrows{position:absolute;left:1075px;top:582px;display:flex;gap:4px}
.slider-arrows span{width:29px;height:17px;border-radius:9px;background:#ddd;font-size:11px;display:flex;align-items:center;justify-content:center;color:#444}

/* who */
.lead-small{font-family:"Montserrat",sans-serif;font-size:20px;color:var(--ink)}
.lead-big{font-family:"Montserrat",sans-serif;font-size:30px;font-weight:500;color:var(--ink)}
.para{font-size:12px;line-height:19px;color:var(--text)}
.value-box{position:absolute;width:245px;height:150px;border:1px solid var(--line);background:#fff;text-align:center;font-family:"Montserrat",sans-serif;font-size:14px;color:var(--ink);padding-top:26px;line-height:19px}
.value-box svg{display:block;margin:0 auto 10px}
.value-box.dark{background:var(--dark);color:#fff;border-color:var(--dark)}

/* services */
.services-band{position:absolute;left:0;top:1097px;width:1200px;height:419px;background:var(--light)}
.svc-label{position:absolute;font-family:"Montserrat",sans-serif;font-size:18px;color:var(--ink)}
.svc-desc{position:absolute;font-size:10px;line-height:15px;color:var(--muted);width:200px}

/* other */
.card-img{position:absolute;width:327px;height:216px}
.card-title{position:absolute;font-family:"Montserrat",sans-serif;font-size:18px;color:var(--ink)}
.card-desc{position:absolute;width:327px;font-size:10.5px;line-height:16px;color:var(--muted)}

/* what we do */
.wwd-band{position:absolute;left:0;top:2032px;width:1200px;height:444px;background:var(--light)}
.wwd-item{position:absolute;width:200px;text-align:center}
.wwd-icon{width:90px;height:90px;border-radius:50%;background:var(--orange);border:4px solid #fbd3bf;margin:0 auto 16px;display:flex;align-items:center;justify-content:center}
.wwd-label{font-family:"Montserrat",sans-serif;font-weight:500;font-size:18px;color:var(--ink)}

/* stats */
.stats{position:absolute;left:0;top:2990px;width:1200px;height:130px;background:linear-gradient(90deg,#2b2b2b,#3a3835 50%,#2b2b2b)}
.stat{position:absolute;top:42px;width:220px;text-align:center}
.stat b{display:block;font-family:"Montserrat",sans-serif;font-size:22px;color:var(--orange);font-weight:700}
.stat span{font-size:11px;color:#fff;letter-spacing:.3px}

/* clients */
.quote-card{position:absolute;background:#fff;box-shadow:0 2px 14px rgba(0,0,0,.12);padding:30px 30px}
.quote-card p{font-size:12.5px;line-height:21px;color:var(--text)}
.who{display:flex;align-items:center;gap:12px;margin-top:22px}
.avatar{width:62px;height:62px;border-radius:50%;background:linear-gradient(135deg,#c9c3bb,#7b736c)}
.who b{display:block;font-family:"Montserrat",sans-serif;font-size:15px;color:var(--ink)}
.who small{font-size:10.5px;color:var(--muted)}

/* footer */
.site-footer{position:absolute;left:0;top:3580px;width:1200px;height:360px;background:#f4f4f4}
.f-col{position:absolute;top:50px}
.f-col h4{font-family:"Montserrat",sans-serif;font-weight:400;font-size:18px;color:var(--ink);padding-bottom:8px;border-bottom:1px solid var(--orange);display:inline-block;margin-bottom:8px}
.f-col p,.f-col li{font-size:10.5px;line-height:17px;color:var(--muted);list-style:none}
.f-col li{margin-bottom:8px}
.f-col .row{display:flex;gap:6px;align-items:flex-start;margin-bottom:20px}
.soc{display:flex;align-items:center;gap:8px;margin-bottom:6px;font-size:11px;color:var(--muted)}
.soc i{width:17px;height:17px;border-radius:50%;background:#555;display:inline-block}
.copyright{position:absolute;left:0;top:3890px;width:1200px;text-align:center;font-size:10.5px;color:var(--muted)}
.copyright em{font-style:normal;color:var(--orange)}
</style>
</head>
<body>

<header class="site-header">
  <div class="brand"><span class="brand-mark"></span><span class="brand-name">SUMMIT BUILDERS</span></div>
  <div class="contact-top">
    <span class="pin"><svg width="11" height="11" viewBox="0 0 12 12"><path d="M1 6 L11 1 L7 11 L6 7 Z" fill="#fff"/></svg></span>
    <div><div class="phone">+1 555 014 2280</div><div class="mail">hello@summitbuildersca.example</div></div>
  </div>
  <div class="quote-btn">GET A QUOTE</div>
  <nav class="main-nav">
    <a class="active">HOME</a><a>ABOUT US</a><a>SERVICES</a><a>PROJECTS / PORTFOLIO</a><a style="margin-right:0">CONTACT US</a>
  </nav>
</header>

<section class="hero">
  <svg class="abs" style="left:0;top:0" width="1200" height="522" viewBox="0 0 1200 522" role="img" aria-label="Photo of a modern kitchen with dark cabinets and marble counters">
    <defs>
      <linearGradient id="heroBg" x1="0" y1="0" x2="1" y2="1">
        <stop offset="0" stop-color="#5e5a55"/><stop offset=".5" stop-color="#3b3835"/><stop offset="1" stop-color="#6d6963"/>
      </linearGradient>
    </defs>
    <polygon points="0,0 1200,0 1200,480 800,522 0,500" fill="url(#heroBg)"/>
    <polygon points="0,0 1200,0 1200,480 800,522 0,500" fill="rgba(0,0,0,.28)"/>
  </svg>
  <div class="hero-copy hero-kicker abs">THE BEST CHOOSE US</div>
  <div class="hero-copy hero-title abs">SUMMIT BUILDERS</div>
  <div class="hero-copy hero-tag abs">Because We Deliver</div>
  <div class="btn btn-orange" style="left:487px;top:317px;width:98px;height:35px">GET STARTED</div>
  <div class="btn btn-white" style="left:604px;top:317px;width:108px;height:35px">CONTACT US</div>
</section>
<div class="slider-arrows"><span>‹</span><span>›</span></div>

<h2 class="section-title" style="top:650px">WHO WE ARE</h2>
<div class="abs" style="left:93px;top:806px;width:475px">
  <div class="lead-small">We Deliver</div>
  <div class="lead-big">Landmark Projects</div>
  <p class="para" style="margin-top:6px">We are rethoric question ran over her cheek When she reached the first hills of the Italic Mountains, she had a last view back on the skyline of her hometown Bookmarksgrove, the headline of Alphabet Village and the subline of her own road, the Line Lane.</p>
</div>
<div class="value-box" style="left:600px;top:722px">
  <svg width="48" height="46" viewBox="0 0 48 46"><polygon points="24,3 30,17 45,18 33,28 37,43 24,35 11,43 15,28 3,18 18,17" fill="none" stroke="var(--orange)" stroke-width="3" stroke-linejoin="round"/></svg>
  We've<br>Repution For Excellence</div>
<div class="value-box" style="left:862px;top:722px">
  <svg width="52" height="46" viewBox="0 0 52 46"><path d="M3 18 L14 10 L24 14 L34 8 L49 18 M10 22 L22 34 Q26 38 30 34 L42 22 M18 28 L24 22 M26 32 L32 26" fill="none" stroke="var(--orange)" stroke-width="3" stroke-linecap="round"/></svg>
  We<br>Build Partnerships</div>
<div class="value-box dark" style="left:600px;top:888px">
  <svg width="48" height="46" viewBox="0 0 48 46"><path d="M5 20 H13 V42 H5 Z M16 20 L24 5 Q29 5 28 12 L27 18 H40 Q44 19 43 24 L39 40 Q38 42 35 42 H16 Z" fill="#fff"/></svg>
  Guided<br>By Commitment</div>
<div class="value-box" style="left:862px;top:888px">
  <svg width="52" height="46" viewBox="0 0 52 46" fill="var(--orange)"><circle cx="15" cy="9" r="6"/><circle cx="37" cy="9" r="6"/><circle cx="26" cy="25" r="6"/><path d="M5 24 Q5 17 15 17 Q25 17 25 24Z M27 24 Q27 17 37 17 Q47 17 47 24Z M15 42 Q15 33 26 33 Q37 33 37 42Z"/></svg>
  A Team<br>Of Professionals</div>

<section class="services-band">
  <svg class="abs" style="left:798px;top:0" width="402" height="419" viewBox="0 0 402 419" role="img" aria-label="Photo of a builder and a homeowner reviewing plans by a brick wall">
    <defs><linearGradient id="svcPhoto" x1="0" y1="0" x2="1" y2="1"><stop offset="0" stop-color="#b79f87"/><stop offset=".6" stop-color="#8a6f59"/><stop offset="1" stop-color="#cfc9c1"/></linearGradient></defs>
    <polygon points="150,0 402,0 402,419 0,419" fill="url(#svcPhoto)"/>
  </svg>
  <div class="abs head" style="left:93px;top:40px;font-size:36px;font-weight:700">OUR SERVICES</div>
  <p class="abs para" style="left:93px;top:82px;width:720px;font-size:11.5px;line-height:18px">Sed ut perspiciatis unde omnis iste natus error sit voluptatem accusantium doloremque laudantium, totam rem aperiam eaque ipsa quae ab illo inventore</p>
  <svg class="abs" style="left:93px;top:147px" width="760" height="152" viewBox="0 0 760 152">
    <polygon points="50,0 282,0 235,152 0,152" fill="#8ea7c4" role="img" aria-label="Photo of a house roof with fire damage"/>
    <polygon points="289,0 520,0 474,152 240,152" fill="#8f8a73" role="img" aria-label="Photo of a residential remodel with a new deck"/>
    <polygon points="526,0 760,0 713,152 480,152" fill="#7f93a8" role="img" aria-label="Photo of a landscaped house with garage"/>
  </svg>
  <div class="svc-label" style="left:94px;top:307px">Fire Damage</div>
  <div class="svc-label" style="left:333px;top:307px">Residential ReModels</div>
  <div class="svc-label" style="left:568px;top:307px">Landscaping and Building</div>
  <div class="svc-desc" style="left:94px;top:334px">If you use this site regularly and would like to help keep the site...</div>
  <div class="svc-desc" style="left:333px;top:334px">If you use this site regularly and would like to help keep the site...</div>
  <div class="svc-desc" style="left:568px;top:334px">If you use this site regularly and would like to help keep the site...</div>
</section>

<h2 class="section-title" style="top:1567px">OTHER SERVICES</h2>
<div class="card-img" style="left:93px;top:1637px;background:linear-gradient(135deg,#9ea3aa,#3d3f47)" role="img" aria-label="Photo of a modern kitchen"></div>
<div class="card-img" style="left:436px;top:1637px;background:linear-gradient(135deg,#c4b49c,#e9e6e1)" role="img" aria-label="Photo of a remodeled bathroom"></div>
<div class="card-img" style="left:779px;top:1637px;background:linear-gradient(135deg,#6f7370,#d6c9a8)" role="img" aria-label="Photo of a room with wooden drawers"></div>
<div class="card-title" style="left:93px;top:1866px">Kitchen</div>
<div class="card-title" style="left:436px;top:1866px">Bathroom</div>
<div class="card-title" style="left:779px;top:1866px">Doors and Drawers</div>
<div class="card-desc" style="left:93px;top:1893px">Sed ut perspiciatis unde omnis iste natus error sit voluptatem accusantium doloremque laudantium</div>
<div class="card-desc" style="left:436px;top:1893px">Sed ut perspiciatis unde omnis iste natus error sit voluptatem accusantium doloremque laudantium</div>
<div class="card-desc" style="left:779px;top:1893px">Sed ut perspiciatis unde omnis iste natus error sit voluptatem accusantium doloremque laudantium</div>
<div class="btn btn-orange" style="left:93px;top:1936px;width:94px;height:34px">READ MORE</div>
<div class="btn btn-orange" style="left:436px;top:1936px;width:94px;height:34px">READ MORE</div>
<div class="btn btn-orange" style="left:779px;top:1936px;width:94px;height:34px">READ MORE</div>

<section class="wwd-band">
  <div class="abs head" style="left:0;top:40px;width:1200px;text-align:center;font-size:36px;font-weight:700">WHAT WE DO</div>
  <svg class="abs" style="left:0;top:0" width="1200" height="444">
    <g stroke="#c8c8c8" stroke-dasharray="2 3" stroke-width="1">
      <line x1="432" y1="150" x2="432" y2="345"/><line x1="769" y1="150" x2="769" y2="345"/>
      <line x1="165" y1="252" x2="360" y2="252"/><line x1="502" y1="252" x2="697" y2="252"/><line x1="839" y1="252" x2="1034" y2="252"/>
    </g>
  </svg>
  <div class="wwd-item" style="left:162px;top:103px"><div class="wwd-icon"><svg width="44" height="44" viewBox="0 0 44 44" fill="#fff"><path d="M22 6 L40 20 H35 V38 H9 V20 H4Z"/></svg></div><div class="wwd-label">Home Construction</div></div>
  <div class="wwd-item" style="left:500px;top:103px"><div class="wwd-icon"><svg width="44" height="44" viewBox="0 0 44 44" fill="#fff"><path d="M22 5 L36 16 V24 H8 V16Z M6 27 H38 V38 H6Z"/></svg></div><div class="wwd-label">Building Remodeling</div></div>
  <div class="wwd-item" style="left:837px;top:103px"><div class="wwd-icon"><svg width="44" height="44" viewBox="0 0 44 44" fill="none" stroke="#fff" stroke-width="3"><rect x="9" y="6" width="26" height="32" rx="2"/><line x1="15" y1="15" x2="29" y2="15"/><line x1="15" y1="22" x2="29" y2="22"/><line x1="15" y1="29" x2="24" y2="29"/></svg></div><div class="wwd-label">Interior Design</div></div>
  <div class="wwd-item" style="left:162px;top:276px"><div class="wwd-icon"><svg width="44" height="44" viewBox="0 0 44 44" fill="#fff"><rect x="8" y="8" width="28" height="30"/><rect x="13" y="13" width="7" height="7" fill="var(--orange)"/><rect x="24" y="13" width="7" height="7" fill="var(--orange)"/><rect x="18" y="26" width="8" height="12" fill="var(--orange)"/></svg></div><div class="wwd-label">Exterior Design</div></div>
  <div class="wwd-item" style="left:500px;top:276px"><div class="wwd-icon"><svg width="44" height="44" viewBox="0 0 44 44" fill="#fff"><path d="M8 20 L22 9 L36 20 V38 H8Z"/><rect x="18" y="26" width="8" height="12" fill="var(--orange)"/><rect x="30" y="4" width="4" height="10"/></svg></div><div class="wwd-label">Renovation</div></div>
  <div class="wwd-item" style="left:837px;top:276px"><div class="wwd-icon"><svg width="44" height="44" viewBox="0 0 44 44" fill="#fff"><path d="M22 5 L36 10 V22 Q36 33 22 40 Q8 33 8 22 V10Z"/><path d="M15 22 L20 27 L29 17" fill="none" stroke="var(--orange)" stroke-width="3"/></svg></div><div class="wwd-label">Safety Management</div></div>
</section>

<h2 class="section-title" style="top:2525px">RECENT WORK</h2>
<div class="abs" style="left:93px;top:2589px;width:250px;height:167px;background:linear-gradient(135deg,#6b4d3a,#d9cbb8)" role="img" aria-label="Photo of a furnished living room"></div>
<div class="abs" style="left:93px;top:2762px;width:250px;height:167px;background:linear-gradient(135deg,#3f4c44,#5fa7b5)" role="img" aria-label="Aerial photo of a house with a pool"></div>
<div class="abs" style="left:349px;top:2589px;width:249px;height:340px;background:linear-gradient(160deg,#ece8e2,#8a6240)" role="img" aria-label="Photo of a staircase in a bright hallway"></div>
<div class="abs" style="left:604px;top:2589px;width:502px;height:340px;background:linear-gradient(160deg,#f2f2f0,#b7b2aa 70%,#8b877f)" role="img" aria-label="Photo of an open-plan kitchen and dining area"></div>

<section class="stats" role="img" aria-label="Dark construction site background">
  <div class="stat" style="left:111px"><b>53</b><span>TOTAL PROJECTS</span></div>
  <div class="stat" style="left:364px"><b>371</b><span>STAFF MEMBERS</span></div>
  <div class="stat" style="left:617px"><b>15</b><span>WORKING IN STATES</span></div>
  <div class="stat" style="left:871px"><b>2,600</b><span>HOURS FOR WORK</span></div>
</section>

<h2 class="section-title" style="top:3166px">OUR CLIENTS</h2>
<div class="quote-card" style="left:93px;top:3230px;width:500px;height:200px">
  <p>"...and for all the wonderful work you and your crew are doing. Our team has nothing but good things to say - we are really fortunate to have found you for this project!"</p>
  <div class="who"><div class="avatar" role="img" aria-label="Client portrait"></div><div><b>Daniel Price</b><small>Chairman RHG</small></div></div>
</div>
<div class="quote-card" style="left:607px;top:3298px;width:499px;height:224px">
  <p>Summit Builders is one of the best general contractors we've worked with. The entire team tactfully delivered a project of exceptional quality while staying on schedule and under budget. We hope to work with Harlow again in the near future!"</p>
  <div class="who"><div class="avatar" role="img" aria-label="Client portrait"></div><div><b>Laura Chen</b><small>Project Manager</small></div></div>
</div>

<footer class="site-footer">
  <div class="f-col" style="left:93px;width:240px">
    <h4>Company</h4>
    <p>We work 7 days a week, every day excluding major holidays. contact us if you have an emergency, with our hotline and contact form.</p>
    <p style="margin-top:14px">Monday – friday:10:00 – 16:00<br>Saturday: 12:00 – 15:00<br>Sunday and holidays:09:00 – 12:00</p>
  </div>
  <div class="f-col" style="left:392px"><h4>Quick Links</h4><ul><li>Home</li><li>About Us</li><li>Services</li><li>Projects / Portfolio</li><li>Contact Us</li></ul></div>
  <div class="f-col" style="left:579px"><h4>What We Do</h4><ul><li>Home Construction</li><li>Building Remodeling</li><li>Interior Design</li><li>Exterior Design</li><li>Renovation</li><li>Safety Management</li></ul></div>
  <div class="f-col" style="left:783px;width:190px">
    <h4>Contact Us</h4>
    <div class="row"><svg width="9" height="12" viewBox="0 0 9 12"><path d="M4.5 0 A4.5 4.5 0 0 1 9 4.5 C9 8 4.5 12 4.5 12 C4.5 12 0 8 0 4.5 A4.5 4.5 0 0 1 4.5 0Z" fill="var(--orange)"/></svg><p>418 Maple Crest Ave, Riverside, CA 92501</p></div>
    <div class="row"><svg width="10" height="10" viewBox="0 0 10 10"><path d="M1 1 L4 1 L5 3.5 L3.5 4.5 Q4.5 6 5.5 6.5 L6.5 5 L9 6 L9 9 Q3 9.5 1 1Z" fill="var(--orange)"/></svg><p>+1 555-014-2280</p></div>
    <div class="row"><svg width="11" height="8" viewBox="0 0 11 8"><rect width="11" height="8" fill="var(--orange)"/><path d="M0 0 L5.5 4.5 L11 0" stroke="#fff" fill="none"/></svg><p>hello@summitbuildersca.example</p></div>
  </div>
  <div class="f-col" style="left:1022px">
    <h4>Follow Us</h4>
    <div class="soc"><i></i>Neighborly</div>
    <div class="soc"><i></i>Chirpline</div>
    <div class="soc"><i></i>WorkLink</div>
    <div class="soc"><i></i>ClipTube</div>
  </div>
  <div class="abs" style="left:0;top:265px;width:1200px;display:flex;justify-content:center;align-items:center;gap:8px">
    <span class="brand-mark"></span><span class="brand-name" style="font-size:16px">SUMMIT BUILDERS</span>
  </div>
</footer>
<div class="copyright">COPYRIGHT © 2020 <em>SUMMIT BUILDERS</em> ALL RIGHTS RESERVED.</div>

</body>
</html>
```